RW Framewell Inc Business cards

We need business cards using our existing logo but slightly modified. Right now the logo says RW Loadbearing Masonry. We want to keep the RW part of the design, but replace the Structural Concrete portion with "FRAMEWELL". Please see the attached file.
Ideally this would be a blank template so we can add Different Names, titles, and phone numbers later.
On the one side we want only the logo and on the other side the detail. I'm attaching an example for you to see.
Please reach out with any other questions. Our address and other details will be given out once we find a design we like.

Target Market(s)

Construction Industry

```html
<!DOCTYPE html>
<html lang="en">
<head>
<meta charset="utf-8">
<title>RW Framewell Inc Business Cards</title>
<link href="https://fonts.googleapis.com/css2?family=Montserrat:wght@600;700&family=Roboto:wght@400;500&display=swap" rel="stylesheet">
<style>
  :root {
    --brand-blue: #2f65ad;
    --brand-grey: #6e6e70;
    --card-white: #fbfbfb;
    --backdrop: #d2d2d2;
    --text-dark: #4a4a4a;
  }
  * { box-sizing: border-box; margin: 0; padding: 0; }
  html, body {
    width: 1200px; height: 852px; overflow: hidden;
    background: var(--backdrop);
  }
  .sheet {
    width: 1200px; height: 852px;
    display: flex; align-items: center; justify-content: center; gap: 60px;
  }
  .card {
    position: relative;
    width: 520px; height: 300px;
    background: var(--card-white);
    border-radius: 18px;
    overflow: hidden;
    box-shadow: 0 10px 24px rgba(0,0,0,0.18);
  }
  .wordmark {
    position: absolute;
    font-family: 'Montserrat', sans-serif;
    font-weight: 700;
    color: var(--brand-blue);
    line-height: 1;
  }
  .wordmark .initials { display: block; font-size: 92px; letter-spacing: -2px; }
  .wordmark .name-line { display: block; font-size: 25px; letter-spacing: 7px; margin-top: 6px; }
  .card--front .wordmark { left: 130px; top: 76px; }
  .front-edge {
    position: absolute; left: 0; right: 0; bottom: 0; height: 14px;
    display: flex;
  }
  .front-edge .edge-grey { width: 44%; background: var(--brand-grey); }
  .front-edge .edge-blue { flex: 1; background: var(--brand-blue); }

  .card--back .wordmark { left: 40px; top: 118px; }
  .card--back .wordmark .initials { font-size: 72px; }
  .card--back .wordmark .name-line { font-size: 19px; letter-spacing: 5px; }
  .back-waves { position: absolute; inset: 0; }
  .holder {
    position: absolute; right: 34px; top: 22px; text-align: right;
    font-family: 'Roboto', sans-serif;
  }
  .holder .person { font-size: 19px; font-weight: 500; color: var(--brand-blue); }
  .holder .role { font-size: 12px; color: var(--text-dark); margin-top: 2px; }
  .holder .address { font-size: 12.5px; color: var(--text-dark); margin-top: 12px; line-height: 1.35; }
  .contact {
    position: absolute; right: 30px; top: 172px;
    list-style: none; text-align: right;
    font-family: 'Roboto', sans-serif; font-size: 12.5px; color: #fff;
  }
  .contact li { display: flex; justify-content: flex-end; align-items: center; gap: 6px; line-height: 20px; }
  .contact svg { width: 11px; height: 11px; fill: none; stroke: #fff; stroke-width: 1.6; }
</style>
</head>
<body>
<main class="sheet">
  <section class="card card--front" aria-label="Card front">
    <div class="wordmark">
      <span class="initials">RW</span>
      <span class="name-line">FRAMEWELL</span>
    </div>
    <div class="front-edge"><span class="edge-grey"></span><span class="edge-blue"></span></div>
  </section>

  <section class="card card--back" aria-label="Card back">
    <svg class="back-waves" viewBox="0 0 520 300" preserveAspectRatio="none" aria-hidden="true">
      <path d="M110,300 C260,294 290,150 520,142 L520,300 Z" fill="var(--brand-blue)"/>
      <path d="M90,268 C265,252 290,126 520,118 L520,129 C310,138 285,260 90,268 Z" fill="var(--brand-grey)"/>
      <path d="M0,272 C40,278 70,274 100,268 C70,282 40,286 0,284 Z" fill="var(--brand-grey)"/>
    </svg>
    <div class="wordmark">
      <span class="initials">RW</span>
      <span class="name-line">FRAMEWELL</span>
    </div>
    <div class="holder">
      <p class="person">Daniel RW Hart</p>
      <p class="role">Managing Director</p>
      <p class="address">88 Sample Road, Any Town,<br>Nevada, US 890123</p>
    </div>
    <ul class="contact">
      <li>555-010-2040
        <svg viewBox="0 0 12 12"><path d="M2 1.5h2.5l1 2.5-1.5 1a6 6 0 0 0 3 3l1-1.5 2.5 1V11A8.5 8.5 0 0 1 1 2.5z"/></svg></li>
      <li>framewell-sample.com
        <svg viewBox="0 0 12 12"><circle cx="6" cy="6" r="5"/><path d="M1 6h10M6 1c2 2.5 2 7.5 0 10M6 1c-2 2.5-2 7.5 0 10"/></svg></li>
      <li>dan@framewell-sample.com
        <svg viewBox="0 0 12 12"><rect x="1" y="2.5" width="10" height="7"/><path d="M1 2.5l5 4 5-4"/></svg></li>
    </ul>
  </section>
</main>
</body>
</html>
```